Corvane Business Cards

Front of business card will have logo, name, address, & telephone number. Back of card will have a list of services provided - Roads, Substation Pads, Temporary Pads, Site Pads, Land Leveling, Powerline Row Cleaning, Land Clearing, Gates, Fencing, Construction Entrances, Excavation, Trenching, Underground Utilities, Directional Boring, Pile Driving. We are a construction company that uses heavy equipment like bulldozers, motor graders/blades, dump trucks, backhoes, hydro axes, & skid loaders. We build roads, pads, & install electric utility lines & waterlines underground. This logo is new. The word "Construction" can be smaller as uploaded 2 example edited logos. We will be using this card design for many employees.
Target Market(s)
Industrial Electric Powerline, Wind Turbine, Solar Panel, & Water Utility companies.
Contact Information for Business Card
Name/Position - Dwayne Halster - Owner
Address: 4875 FM 309
Brennick, TX 79412
Phone number - (325) 482-5096

```html
<!DOCTYPE html>
<html lang="en">
<head>
<meta charset="utf-8">
<title>Corvane Construction – Business Card</title>
<link rel="stylesheet" href="https://fonts.googleapis.com/css2?family=Roboto:ital,wght@0,300;0,400;0,700;0,900;1,300&display=swap">
<style>
  :root {
    --stage: #1d1d1f;
    --card: #3b111a;
    --ink: #ffffff;
    --ink-soft: rgba(255,255,255,0.85);
  }
  * { margin: 0; padding: 0; box-sizing: border-box; }
  html, body { width: 1200px; height: 900px; overflow: hidden; }
  body {
    background: var(--stage);
    font-family: "Roboto", Arial, sans-serif;
    color: var(--ink);
    position: relative;
  }
  .card {
    position: absolute;
    left: 240px;
    width: 720px;
    height: 411px;
    background: var(--card);
    border-radius: 3px;
  }
  .card--front { top: 30px; }
  .card--back { top: 459px; }

  /* Front */
  .holder {
    position: absolute;
    left: 60px;
    top: 100px;
  }
  .holder__name {
    font-size: 26px;
    font-weight: 900;
    text-transform: uppercase;
    letter-spacing: 1px;
  }
  .holder__role {
    font-size: 18px;
    font-weight: 300;
    font-style: italic;
    margin-top: 4px;
    color: var(--ink-soft);
  }
  .divider {
    position: absolute;
    left: 60px;
    top: 182px;
    width: 480px;
    height: 1px;
    background: linear-gradient(90deg, var(--ink) 0%, var(--ink) 70%, rgba(255,255,255,0) 100%);
  }
  .contact {
    position: absolute;
    left: 60px;
    top: 204px;
    display: flex;
    gap: 44px;
    font-size: 18px;
    font-weight: 400;
  }
  .contact__item { display: flex; align-items: center; gap: 8px; white-space: nowrap; }
  .contact__item svg { width: 16px; height: 16px; fill: var(--ink); }
  .wordmark {
    position: absolute;
    right: 56px;
    bottom: 70px;
    text-align: right;
    text-transform: uppercase;
    font-weight: 400;
    letter-spacing: 3px;
    line-height: 1.1;
  }
  .wordmark__name { font-size: 26px; }
  .wordmark__tag { font-size: 34px; }

  /* Back */
  .back-mark {
    position: absolute;
    right: 60px;
    top: 50px;
    font-size: 66px;
    font-weight: 700;
    letter-spacing: 5px;
    text-transform: uppercase;
  }
  .services {
    position: absolute;
    right: 60px;
    top: 196px;
    text-align: right;
    font-size: 17px;
    font-weight: 400;
    line-height: 1.65;
    list-style: none;
  }
</style>
</head>
<body>
  <section class="card card--front" aria-label="Business card front">
    <div class="holder">
      <div class="holder__name">Dwayne Halster</div>
      <div class="holder__role">Owner</div>
    </div>
    <div class="divider"></div>
    <div class="contact">
      <div class="contact__item">
        <svg viewBox="0 0 24 24" aria-hidden="true"><path d="M6.6 10.8a15.1 15.1 0 0 0 6.6 6.6l2.2-2.2a1 1 0 0 1 1-.25 11.4 11.4 0 0 0 3.6.57 1 1 0 0 1 1 1V20a1 1 0 0 1-1 1A17 17 0 0 1 3 4a1 1 0 0 1 1-1h3.5a1 1 0 0 1 1 1c0 1.25.2 2.45.57 3.57a1 1 0 0 1-.25 1z"/></svg>
        <span>(325) 482-5096</span>
      </div>
      <div class="contact__item">
        <svg viewBox="0 0 24 24" aria-hidden="true"><path d="M12 2a7 7 0 0 0-7 7c0 5.25 7 13 7 13s7-7.75 7-13a7 7 0 0 0-7-7zm0 9.5a2.5 2.5 0 1 1 0-5 2.5 2.5 0 0 1 0 5z"/></svg>
        <span>4875 FM 309 Brennick, TX 79412</span>
      </div>
    </div>
    <div class="wordmark">
      <div class="wordmark__name">Corvane</div>
      <div class="wordmark__tag">Construction</div>
    </div>
  </section>

  <section class="card card--back" aria-label="Business card back">
    <div class="back-mark">Corvane</div>
    <ul class="services">
      <li>Roads / Substation Pads / Temporary Pads / Site Pads / Land Leveling</li>
      <li>Land Clearing / Gates / Fencing / Construction Entrances / Excavation / Trenching</li>
      <li>Underground Utilities / Powerline Row Cleaning / Pile Driving / Directional Boring</li>
    </ul>
  </section>
</body>
</html>
```